Tovel & Associates - London New Letting and Property Management Company *

Tovel & Associates LTD is a new company based in London, and works with brand new residential property in the city centre.

We are aiming to have 1000 new properties a year.

We are looking for something modern and minimalistic :
Logo ,Monogram, Paper Head and Business Card.

Target Market(s)

Internation landlords

Industry/Entity Type

Real Estate

Logo Text

Tovel & Associates

Colors

Designer to choose colors to be used in the design.

Requirements
Nice to have
• A particular monogram with "TA"
Should not have
• Little House over the logo

```html
<!DOCTYPE html>
<html lang="en">
<head>
<meta charset="utf-8">
<title>Tovel &amp; Associates — Stationery</title>
<link rel="stylesheet" href="https://fonts.googleapis.com/css2?family=Work+Sans:wght@400;500;600&display=swap">
<style>
  :root{
    --bg:#dcdcdc;
    --paper:#f3f3f3;
    --navy:#1b4f72;
    --sky:#29a9e1;
    --ink:#5e5e5e;
    --ink-dark:#4a4a4a;
    --white:#ffffff;
  }
  *{margin:0;padding:0;box-sizing:border-box}
  html,body{width:1200px;height:1062px;overflow:hidden;background:var(--bg)}
  body{position:relative;font-family:"Work Sans",sans-serif;color:var(--ink)}
  .abs{position:absolute}

  /* brand mark: plain square + name */
  .brand-square{position:absolute;background:var(--navy)}
  .brand-name{position:absolute;font-weight:600;color:var(--navy);white-space:nowrap;letter-spacing:.04em;text-transform:uppercase}

  /* letterhead */
  .letterhead{left:115px;top:94px;width:620px;height:876px;background:var(--paper)}
  .letterhead .brand-square{left:469px;top:36px;width:107px;height:107px}
  .letterhead .brand-name{right:44px;top:150px;font-size:9.6px}
  .salutation{left:44px;top:178px;font-size:18px;color:var(--ink)}
  .body-copy{left:44px;width:532px;font-size:12px;line-height:16.1px;color:var(--ink)}
  .p1{top:232px}.p2{top:316px}.p3{top:432px}.p4{top:518px}
  .closing{left:44px;top:616px;font-size:15px;color:var(--ink-dark);letter-spacing:-.02em}
  .signature{left:44px;top:647px;width:112px;height:16px;background:linear-gradient(90deg,#9a9a9a,#c4c4c4);opacity:.55;border-radius:8px}
  .signer{left:44px;top:675px;font-size:13.5px;color:var(--ink-dark);letter-spacing:-.02em}
  .signer-role{left:44px;top:692px;font-size:11px;color:var(--ink-dark);letter-spacing:-.02em}
  .signer-co{left:44px;top:710px;font-size:7.6px;font-weight:500;color:var(--ink-dark);text-transform:uppercase;letter-spacing:-.01em}
  .rule{height:1.5px;background:var(--navy)}
  .letterhead .rule{left:38px;top:765px;width:538px}
  .contact{font-size:11.5px;line-height:15px;color:var(--ink)}
  .contact li{list-style:none;display:flex;align-items:center;gap:5px}
  .contact svg{width:7px;height:7px;flex:none}
  .contact .web{color:var(--navy)}
  .letterhead .contact{left:38px;top:789px}
  .address{text-align:right;font-size:11.5px;line-height:15px}
  .letterhead .address{right:44px;top:804px}
  .bar-dark{background:var(--navy)}
  .bar-light{background:var(--sky)}
  .letterhead .bar-dark{left:0;bottom:0;width:307px;height:16px}
  .letterhead .bar-light{left:312px;bottom:0;width:308px;height:16px}

  /* standalone mark */
  .mark-large .brand-square{left:878px;top:152px;width:212px;height:212px}
  .mark-large .brand-name{left:878px;top:373px;width:212px;text-align:center;font-size:16.5px;letter-spacing:.02em}

  /* business card front */
  .card-front{left:716px;top:475px;width:374px;height:213px;background:var(--paper)}
  .card-front .brand-square{left:18px;top:17px;width:90px;height:90px}
  .card-front .brand-name{left:18px;top:110px;font-size:7.4px;letter-spacing:.02em}
  .holder{right:20px;top:104px;font-size:14.5px;font-weight:500;color:var(--navy);letter-spacing:.02em;text-transform:uppercase}
  .holder-role{right:20px;top:123px;font-size:8.5px;color:var(--ink)}
  .card-front .rule{left:18px;top:142px;width:336px;height:1px}
  .card-front .contact{left:18px;top:155px;font-size:8.8px;line-height:13px}
  .card-front .contact svg{width:5px;height:5px}
  .card-front .address{right:20px;top:168px;font-size:8.8px;line-height:13px}
  .card-front .bar-dark{left:0;bottom:0;width:185px;height:6px}
  .card-front .bar-light{left:188px;bottom:0;width:186px;height:6px}

  /* business card back */
  .card-back{left:716px;top:726px;width:374px;height:213px;background:var(--navy)}
  .card-back .brand-square{left:136px;top:49px;width:102px;height:102px;background:var(--white)}
  .card-back .brand-name{left:0;width:374px;text-align:center;top:154px;font-size:8.4px;color:var(--white);letter-spacing:.02em}
</style>
</head>
<body>

<section class="abs letterhead" aria-label="Letterhead">
  <div class="brand-square"></div>
  <div class="brand-name">Tovel &amp; Associates</div>

  <p class="abs salutation">Dear Sir</p>

  <p class="abs body-copy p1">Lorem ipsum dolor sit amet, an vel recteque dissentiet, detracto albucius platonem ex vel, eros repudiandae cu. Atqui aliquando nec an, unum graece adolescens vel ad. Id odio scae has, iudico euismod atomorum ius ea, cum ea honestatis quaerendum theophrastus. Mea honestatis quaerendum theophrastus. Mea</p>
  <p class="abs body-copy p2">Lorem ipsum dolor sit amet, an vel recteque dissentiet, detracto albucius platonem ex vel, eros repudiandae cu. Atqui aliquando nec an, unum graece adolescens vel ad. Id odio scae has, iudico euismod atomorum ius ea, cum ea honestatis quaerendum theophrastus. Mea doming repudiandae ex, cu cum civibus assentior posidonium. Quo etiam pertinax ex, te eros repudiandae cu. Atqui aliquando nec an, unum graece adolescens vel ad. Id odio scae honestatis quaerendum theophrastus. Mea</p>
  <p class="abs body-copy p3">Lorem ipsum dolor sit amet, an vel recteque dissentiet, detracto albucius platonem ex vel, eros repudiandae cu. Atqui aliquando nec an, unum graece adolescens vel ad. Id odio scae has, iudico euismod atomorum ius ea, cum ea honestatis quaerendum theophrastus. Mea honestatis quaerendum theophrastus. Mea</p>
  <p class="abs body-copy p4">Lorem ipsum dolor sit amet, an vel recteque dissentiet, detracto albucius platonem ex vel, eros repudiandae cu. Atqui aliquando nec an, unum graece adolescens vel ad. Id odio scae has, iudico euismod atomorum ius ea, cum ea honestatis quaerendum theophrastus. Mea honestatis quaerendum theophrastus. Mea</p>

  <p class="abs closing">Kind Regards</p>
  <div class="abs signature" role="img" aria-label="Handwritten signature"></div>
  <p class="abs signer">Daniel Whitcombe</p>
  <p class="abs signer-role">Managing Partner</p>
  <p class="abs signer-co">Harrowgate Property Holdings LTD</p>

  <div class="abs rule"></div>
  <ul class="abs contact">
    <li><svg viewBox="0 0 10 10"><path d="M2 1h2l1 2.5-1.3 1a5 5 0 0 0 2 2l1-1.3L9 6v2c0 .6-.5 1-1 1A8 8 0 0 1 1 2c0-.5.4-1 1-1z" fill="currentColor"/></svg>+44 20 7946 0318</li>
    <li><svg viewBox="0 0 10 10"><rect x="1" y="2" width="8" height="6" fill="none" stroke="currentColor" stroke-width="1.2"/><path d="M1 2l4 3 4-3" fill="none" stroke="currentColor" stroke-width="1.2"/></svg>info@tovelassociates.co.uk</li>
    <li><svg viewBox="0 0 10 10"><circle cx="5" cy="5" r="4" fill="currentColor"/></svg><span>www.<span class="web">tovelassociates</span>.co.uk</span></li>
  </ul>
  <p class="abs address">14 Harcourt Row<br>London W1K 4QT</p>

  <div class="abs bar-dark"></div>
  <div class="abs bar-light"></div>
</section>

<section class="mark-large" aria-label="Brand mark">
  <div class="brand-square"></div>
  <div class="brand-name">Tovel &amp; Associates</div>
</section>

<section class="abs card-front" aria-label="Business card front">
  <div class="brand-square"></div>
  <div class="brand-name">Tovel &amp; Associates</div>
  <p class="abs holder">Oliver Brandt</p>
  <p class="abs holder-role">Director</p>
  <div class="abs rule"></div>
  <ul class="abs contact">
    <li><svg viewBox="0 0 10 10"><path d="M2 1h2l1 2.5-1.3 1a5 5 0 0 0 2 2l1-1.3L9 6v2c0 .6-.5 1-1 1A8 8 0 0 1 1 2c0-.5.4-1 1-1z" fill="currentColor"/></svg>+44 20 7946 0318</li>
    <li><svg viewBox="0 0 10 10"><rect x="1" y="2" width="8" height="6" fill="none" stroke="currentColor" stroke-width="1.2"/><path d="M1 2l4 3 4-3" fill="none" stroke="currentColor" stroke-width="1.2"/></svg>info@tovelassociates.co.uk</li>
    <li><svg viewBox="0 0 10 10"><circle cx="5" cy="5" r="4" fill="currentColor"/></svg><span>www.<span class="web">tovelassociates</span>.co.uk</span></li>
  </ul>
  <p class="abs address">14 Harcourt Row<br>London W1K 4QT</p>
  <div class="abs bar-dark"></div>
  <div class="abs bar-light"></div>
</section>

<section class="abs card-back" aria-label="Business card back">
  <div class="brand-square"></div>
  <div class="brand-name">Tovel &amp; Associates</div>
</section>

</body>
</html>
```